Lunelle Rosa Hair Fancy Business Card’s

I want my business cards to be elite, original and very classy. I want the business cards to match the colors of my logo and to match the design posted. I would love the design of the picture I posted

I want the card all white .
The dripping on the top of the card I want it to match the pink color in my logo that’s also posted .
I need my logo on the business card !
I need my Instagram- @lunelle.rosa.hair__
And my phone number - 555 207 3962

Target Market(s)

My target market is young woman age 23 to older woman to the age of 65
I want both older and younger women to love my design . I don’t want any cheap looking business cards

Industry/Entity Type

Hair And Beauty

Contact Information for Business Card

Add my logo
Add my Instagram- @lunelle.rosa.hair__
My number - 555 207 3962
My website- www.lunellerosahair.example

Font styles to use
Serif
Script

Colors
ffffff
e667a6
e34298

Requirements
Must have
• The business cards must have my logo, my number , my website, and my Instagram!
Nice to have
• Nice to have glitter words that match my logo
• The business cards must look classy and mature
• I want them to be very unique!!
Should not have
• Should not have any colors that doesn’t match my logo ! This is very important! Please

```html
<!DOCTYPE html>
<html lang="en">
<head>
<meta charset="utf-8">
<title>Lunelle Rosa Hair — Business Card</title>
<link href="https://fonts.googleapis.com/css2?family=Oswald:wght@500&family=Poppins:wght@400&display=swap" rel="stylesheet">
<style>
  :root {
    --backdrop: #242424;
    --card-white: #ffffff;
    --brand-pink: #e34298;
    --soft-pink: #e667a6;
    --sparkle-light: #c98ab8;
    --sparkle-deep: #a2628f;
    --text-light: #ffffff;
  }
  * { margin: 0; padding: 0; box-sizing: border-box; }
  html, body {
    width: 1125px;
    height: 1200px;
    overflow: hidden;
    background: var(--backdrop);
  }
  .canvas {
    position: relative;
    width: 1125px;
    height: 1200px;
  }
  .card {
    position: absolute;
    left: 171px;
    width: 826px;
    height: 472px;
    background: var(--card-white);
    overflow: hidden;
  }
  .card--front { top: 106px; }
  .card--back { top: 639px; }

  .sparkle-panel {
    position: absolute;
    left: 0;
    width: 100%;
    background: linear-gradient(180deg, var(--sparkle-deep), var(--sparkle-light) 50%, var(--sparkle-deep));
  }
  .sparkle-panel--top { top: 0; height: 145px; }
  .sparkle-panel--bottom { top: 326px; height: 146px; }

  .contact-band {
    position: absolute;
    left: 0;
    top: 145px;
    width: 100%;
    height: 181px;
    background: var(--brand-pink);
    color: var(--text-light);
  }
  .identity {
    position: absolute;
    right: 454px;
    top: 54px;
    text-align: right;
    font-family: "Oswald", sans-serif;
    font-weight: 500;
    text-transform: uppercase;
    line-height: 1;
  }
  .identity__name { font-size: 37px; letter-spacing: 0.3px; }
  .identity__role { font-size: 19px; margin-top: 3px; }
  .divider {
    position: absolute;
    left: 391px;
    top: 43px;
    width: 2px;
    height: 98px;
    background: var(--text-light);
  }
  .contact-list {
    position: absolute;
    left: 411px;
    top: 44px;
    list-style: none;
    font-family: "Poppins", sans-serif;
    font-size: 18.5px;
    line-height: 24px;
  }
  .contact-list li { display: flex; align-items: center; gap: 11px; }
  .contact-list svg { width: 14px; height: 14px; flex: none; fill: var(--text-light); }

  .wordmark {
    position: absolute;
    left: 0;
    top: 0;
    width: 100%;
    height: 100%;
    display: flex;
    flex-direction: column;
    align-items: center;
    justify-content: center;
    font-family: "Poppins", sans-serif;
    font-weight: 400;
    font-size: 64px;
    line-height: 1.15;
    letter-spacing: 3px;
    color: var(--brand-pink);
    text-align: center;
  }
</style>
</head>
<body>
<main class="canvas">
  <section class="card card--front" aria-label="Business card front">
    <div class="sparkle-panel sparkle-panel--top" role="img" aria-label="Pink glitter texture"></div>
    <div class="contact-band">
      <div class="identity">
        <p class="identity__name">Daniel Brooks</p>
        <p class="identity__role">President</p>
      </div>
      <div class="divider"></div>
      <ul class="contact-list">
        <li>
          <svg viewBox="0 0 24 24" aria-hidden="true"><path d="M6.6 10.8a15.1 15.1 0 0 0 6.6 6.6l2.2-2.2a1 1 0 0 1 1-.25 11.4 11.4 0 0 0 3.6.57 1 1 0 0 1 1 1V20a1 1 0 0 1-1 1A17 17 0 0 1 3 4a1 1 0 0 1 1-1h3.5a1 1 0 0 1 1 1c0 1.25.2 2.45.57 3.57a1 1 0 0 1-.25 1z"/></svg>
          555 207 3962
        </li>
        <li>
          <svg viewBox="0 0 24 24" aria-hidden="true"><path d="M2 5h20v14H2zm2 2v.5l8 5.5 8-5.5V7z" fill-rule="evenodd"/></svg>
          info@lunellerosahair.example
        </li>
        <li>
          <svg viewBox="0 0 24 24" aria-hidden="true"><circle cx="12" cy="12" r="10"/><path d="M2 12h20M12 2c3 3 3 17 0 20M12 2c-3 3-3 17 0 20" fill="none" stroke="#e34298" stroke-width="1.5"/></svg>
          www.lunellerosahair.example
        </li>
        <li>
          <svg viewBox="0 0 24 24" aria-hidden="true"><rect x="3" y="3" width="18" height="18" rx="2"/></svg>
          @lunelle.rosa.hair__
        </li>
      </ul>
    </div>
    <div class="sparkle-panel sparkle-panel--bottom" role="img" aria-label="Pink glitter texture"></div>
  </section>

  <section class="card card--back" aria-label="Business card back">
    <p class="wordmark"><span>Lunelle Rosa</span><span>Hair</span></p>
  </section>
</main>
</body>
</html>
```